Healthy lifestyle Influencer business card

I need your creativity to have a business card that I can leave in all the restaurants, hotels and spas I visit to inform them that I am an influencer specializing in the wellness sector and that I will write a review about them. You can use my instagram photos Lunavita27 or on my website www.piattileggeriorto.it. I would like my business card to impress with its creativity! thank you very much!

Contact Information for Business Card

siteweb, instagram, phone number

Font styles to use
Decorative
Script

Colors
0094D4
00A9DD
6FCCEA
C7EBF8
E9F6FB
59FF00
82FF00
B8FF75
E3FFCB
F4FFEA
FFC000
F8CF3A
FAE287
FDF2CF
FEFAEE
F0912C
F2A743
F7CA91
FBE8D2
FDF5EE
EE7325
F08F49
F5BC92
FAE3D3
FDF4ED
EB3D1F
EC4F4E
F09395
F8D3D4
FCEDEE
E54698
E96AAD
F1A4CE
F9D9EA
FCEFF6

Requirements
Nice to have
• creativity

```html
<!DOCTYPE html>
<html lang="it">
<head>
<meta charset="utf-8">
<title>Luna Moretti – Biglietto da visita</title>
<link rel="stylesheet" href="https://fonts.googleapis.com/css2?family=Josefin+Sans:wght@300;600&display=swap">
<style>
  :root {
    --backdrop: #efabac;
    --coral: #e8475a;
    --raspberry: #e2395f;
    --brand-ink: #5a2a34;
    --white: #ffffff;
    --icon-ink: #d63a55;
  }
  * { margin: 0; padding: 0; box-sizing: border-box; }
  html, body { width: 1200px; height: 1200px; overflow: hidden; }
  body {
    background: var(--backdrop);
    font-family: "Josefin Sans", sans-serif;
    position: relative;
  }
  .card {
    position: absolute;
    left: 225px;
    width: 750px;
    height: 428px;
    overflow: hidden;
  }
  .card--front { top: 100px; }
  .card--back { top: 650px; }
  .card > svg { position: absolute; inset: 0; width: 750px; height: 428px; }

  .brand {
    position: absolute;
    left: 460px;
    top: 78px;
    width: 270px;
    text-align: center;
    color: var(--brand-ink);
  }
  .brand__name {
    display: flex;
    align-items: center;
    justify-content: center;
    gap: 10px;
    font-weight: 600;
    font-size: 30px;
    letter-spacing: 0.5px;
    line-height: 1;
  }
  .brand__dot {
    width: 10px; height: 10px; border-radius: 50%;
    background: var(--brand-ink);
  }
  .brand__tagline {
    margin-top: 14px;
    font-weight: 600;
    font-size: 12px;
    letter-spacing: 0.3px;
  }

  .holder-name {
    position: absolute;
    left: 85px;
    top: 70px;
    color: var(--white);
    font-weight: 300;
    font-size: 50px;
    letter-spacing: 0.5px;
  }
  .contact {
    position: absolute;
    display: flex;
    align-items: center;
    gap: 18px;
    color: var(--white);
    font-weight: 300;
    font-size: 23px;
    letter-spacing: 0.4px;
  }
  .contact--phone { left: 249px; top: 199px; }
  .contact--social { left: 295px; top: 247px; }
  .contact--web { left: 337px; top: 296px; }
  .contact__icon {
    width: 34px; height: 34px; border-radius: 50%;
    background: var(--white);
    display: flex; align-items: center; justify-content: center;
    flex: none;
  }
  .contact__icon svg { width: 20px; height: 20px; }
</style>
</head>
<body>

<section class="card card--front">
  <svg viewBox="0 0 750 428">
    <defs>
      <linearGradient id="front-bg" x1="0" y1="1" x2="1" y2="0">
        <stop offset="0" stop-color="#b82442"/>
        <stop offset="0.55" stop-color="#e8475a"/>
        <stop offset="1" stop-color="#e2395f"/>
      </linearGradient>
      <linearGradient id="front-portrait" x1="0" y1="1" x2="1" y2="0">
        <stop offset="0" stop-color="#6e1636"/>
        <stop offset="1" stop-color="#9c2240"/>
      </linearGradient>
      <linearGradient id="silver" x1="0" y1="0" x2="1" y2="1">
        <stop offset="0" stop-color="#a8a8a8"/>
        <stop offset="0.5" stop-color="#f4f4f4"/>
        <stop offset="1" stop-color="#b4b4b4"/>
      </linearGradient>
      <radialGradient id="glint">
        <stop offset="0" stop-color="#fff" stop-opacity="0.95"/>
        <stop offset="1" stop-color="#fff" stop-opacity="0"/>
      </radialGradient>
    </defs>
    <rect width="750" height="428" fill="url(#front-bg)"/>
    <polygon points="0,0 233,0 655,428 0,428" fill="url(#front-portrait)"
             role="img" aria-label="Illustrazione stilizzata di una donna con lunghi capelli mossi"/>
    <polygon points="233,0 285,0 705,428 655,428" fill="url(#silver)"/>
    <polygon points="535,300 560,322 488,428 458,428" fill="url(#silver)"/>
    <ellipse cx="480" cy="205" rx="60" ry="22" fill="url(#glint)"/>
    <ellipse cx="460" cy="385" rx="40" ry="14" fill="url(#glint)"/>
  </svg>
  <div class="brand">
    <div class="brand__name"><span class="brand__dot"></span>Orto di Luna</div>
    <div class="brand__tagline">Sapori leggeri ogni giorno</div>
  </div>
</section>

<section class="card card--back">
  <svg viewBox="0 0 750 428">
    <defs>
      <linearGradient id="back-bg" x1="0" y1="0" x2="1" y2="1">
        <stop offset="0" stop-color="#e8475a"/>
        <stop offset="0.6" stop-color="#e2395f"/>
        <stop offset="1" stop-color="#d8344c"/>
      </linearGradient>
      <linearGradient id="back-hair" x1="0" y1="0" x2="1" y2="1">
        <stop offset="0" stop-color="#8a1e3c"/>
        <stop offset="1" stop-color="#5a1428"/>
      </linearGradient>
      <linearGradient id="silver-b" x1="0" y1="0" x2="1" y2="1">
        <stop offset="0" stop-color="#a8a8a8"/>
        <stop offset="0.5" stop-color="#f4f4f4"/>
        <stop offset="1" stop-color="#b4b4b4"/>
      </linearGradient>
      <radialGradient id="glint-b">
        <stop offset="0" stop-color="#fff" stop-opacity="0.95"/>
        <stop offset="1" stop-color="#fff" stop-opacity="0"/>
      </radialGradient>
    </defs>
    <rect width="750" height="428" fill="url(#back-bg)"/>
    <polygon points="0,118 310,428 0,428" fill="url(#back-hair)"
             role="img" aria-label="Decorazione di ciocche di capelli mossi"/>
    <polygon points="455,0 750,0 750,290" fill="url(#back-hair)"
             role="img" aria-label="Decorazione di ciocche di capelli mossi"/>
    <polygon points="0,80 345,428 310,428 0,118" fill="url(#silver-b)"/>
    <polygon points="405,0 455,0 750,290 750,340" fill="url(#silver-b)"/>
    <ellipse cx="140" cy="220" rx="55" ry="20" fill="url(#glint-b)"/>
    <ellipse cx="580" cy="170" rx="55" ry="20" fill="url(#glint-b)"/>
  </svg>

  <h1 class="holder-name">Luna Moretti</h1>

  <div class="contact contact--phone">
    <span class="contact__icon">
      <svg viewBox="0 0 24 24"><path fill="#d63a55" d="M6.6 10.8a15.1 15.1 0 0 0 6.6 6.6l2.2-2.2a1 1 0 0 1 1-.25 11.4 11.4 0 0 0 3.6.57 1 1 0 0 1 1 1V20a1 1 0 0 1-1 1A17 17 0 0 1 3 4a1 1 0 0 1 1-1h3.5a1 1 0 0 1 1 1c0 1.25.2 2.45.57 3.57a1 1 0 0 1-.25 1z"/></svg>
    </span>
    <span>008 412 730 2195</span>
  </div>
  <div class="contact contact--social">
    <span class="contact__icon"></span>
    <span>Lunavita27</span>
  </div>
  <div class="contact contact--web">
    <span class="contact__icon">
      <svg viewBox="0 0 24 24" fill="none" stroke="#d63a55" stroke-width="2"><circle cx="12" cy="12" r="9"/><path d="M3 12h18M12 3c3 3.2 3 14.8 0 18M12 3c-3 3.2-3 14.8 0 18"/></svg>
    </span>
    <span>piattileggeriorto.it</span>
  </div>
</section>

</body>
</html>
```